Transform Your Giving

I need a tri-fold brochure that will fit in a standard number 10 business envelope. Meadowlark and Allied Services is a charitable nonprofit. The goal of this brochure is to stimulate people into thinking about other ways to make a donation. The design should communicate the essential information on donation options, create a sense of professional integrity, be graphically sharp, easy to read and laid out in a way that doesn't make the material appear crowded.

```html
<!DOCTYPE html>
<html lang="en">
<head>
<meta charset="utf-8">
<title>Transform Your Giving – Tri-fold Brochure</title>
<link rel="stylesheet" href="https://fonts.googleapis.com/css2?family=Bebas+Neue&family=Montserrat:ital,wght@0,400;0,500;0,600;0,700;1,500;1,600&display=swap">
<style>
:root{
  --purple-deep:#231d5e;
  --purple:#2d2675;
  --purple-light:#4a3ba6;
  --green:#4cb944;
  --green-dark:#3a9f35;
  --ink:#1f1d3a;
  --paper:#ffffff;
  --backdrop:#ececec;
}
*{box-sizing:border-box;margin:0;padding:0}
html,body{width:720px;height:1200px;overflow:hidden;background:var(--backdrop)}
body{position:relative;font-family:"Montserrat",Arial,sans-serif;color:var(--ink)}
.sheet{position:absolute;left:53px;width:614px;height:474px;display:flex;box-shadow:0 3px 8px rgba(0,0,0,.18);background:var(--paper)}
.sheet--outside{top:123px}
.sheet--inside{top:625px}
.panel{position:relative;width:205px;height:100%;overflow:hidden}
.panel--purple{background:radial-gradient(ellipse at 60% 55%,var(--purple-light) 0%,var(--purple) 55%,var(--purple-deep) 100%);color:#fff}
.abs{position:absolute}
.body-text{font-size:5.9px;line-height:7.4px;font-weight:500}
.photo{position:absolute}
.pill{position:absolute;background:var(--green);color:#fff;font-weight:700;font-size:7.4px;letter-spacing:.2px;padding:2px 5px;border-radius:6px;white-space:nowrap}
.section-head{position:absolute;color:var(--green);font-weight:600;font-size:7.6px;line-height:9px}
.section-head em{display:block;font-weight:600;font-size:5.8px;line-height:7.3px}
.checklist{list-style:none}
.checklist li{position:relative;padding-left:9px}
.checklist li::before{content:"";position:absolute;left:0;top:1.5px;width:4px;height:4px;border:.7px solid currentColor;border-radius:.5px}
.brand-name{font-weight:700;text-align:center;letter-spacing:.3px}
</style>
</head>
<body>

<!-- OUTSIDE -->
<section class="sheet sheet--outside">

  <!-- Inside flap: impact of your gift -->
  <div class="panel">
    <div class="photo" role="img" aria-label="Photo of a smiling woman with glasses reading a book outdoors" style="left:0;top:0;width:205px;height:330px;background:linear-gradient(160deg,#8a7a3c 0%,#c9a582 40%,#e6bcb8 70%,#b99b7a 100%)"></div>
    <svg class="abs" style="left:0;top:270px" width="205" height="80" viewBox="0 0 205 80">
      <path d="M0 40 Q90 -10 205 60 L205 80 L0 80Z" fill="var(--green)"/>
      <path d="M0 50 Q95 5 205 75 L205 80 L0 80Z" fill="#fff"/>
    </svg>
    <div class="abs" style="left:0;top:314px;width:141px;height:21px;background:var(--purple);border-radius:0 10px 10px 0;color:#fff;font-family:'Bebas Neue',sans-serif;font-size:16px;line-height:21px;padding-left:14px">THE IMPACT OF YOUR GIFT</div>
    <p class="abs body-text" style="left:14px;top:347px;width:176px">Your generosity drives our mission. With every Smart gift you're supporting Meadowlark and Allied Services. Join our community of Smart Givers today and make an enduring impact. With Smart Giving your generosity reaches further. Begin your Smart Giving journey with us today.</p>
    <ul class="abs checklist body-text" style="left:14px;top:401px;font-weight:600;line-height:13.1px">
      <li>Stocks and Securities</li><li>DAFs</li><li>QCDs</li><li>Crypto</li><li>Charitable Annuity</li>
    </ul>
  </div>

  <!-- Back panel: contact -->
  <div class="panel panel--purple">
    <p class="abs body-text" style="left:14px;top:14px;width:177px;text-align:center">To learn more about Smart Giving Options and how they can benefit you and Meadowlark and Allied Services, please reach out to our team. We're here to help you navigate these giving methods and answer any question you may have.</p>
    <div class="abs" style="left:15px;top:65px;width:177px;height:61px;background:#fff;border-radius:12px"></div>
    <svg class="abs" style="left:15px;top:65px" width="177" height="61" viewBox="0 0 177 61">
      <text x="6" y="20" fill="var(--green)" font-family="Montserrat" font-weight="700" font-size="22">&#8220;</text>
      <path d="M36 11 H168 Q172 11 172 15 V39 Q172 46 165 46" fill="none" stroke="var(--green)" stroke-width=".8"/>
      <text x="80" y="58" fill="var(--green)" font-family="Montserrat" font-weight="700" font-size="22">&#8221;</text>
      <path d="M108 46 H150" stroke="var(--green)" stroke-width=".8"/>
    </svg>
    <p class="abs" style="left:21px;top:84px;width:160px;color:var(--purple-light);font-size:7.4px;line-height:9.4px;font-style:italic;font-weight:500">Being kind to others is a way of being good to yourself.<br><b style="font-weight:700;color:var(--purple)">- Helen Marsh</b></p>
    <div class="abs brand-name" style="left:0;top:146px;width:205px;font-size:13px;color:#fff">Meadowlark &amp; Allied</div>
    <div class="abs" style="left:0;top:163px;width:205px;text-align:center;font-size:3.6px;font-weight:700;letter-spacing:.3px">MEADOWLARK AND ALLIED SERVICES, INC.</div>
    <div class="abs" style="left:27px;top:196px;width:152px;height:29px;background:var(--green);border-radius:7px;text-align:center;font-size:5.9px;line-height:7.4px;font-weight:500;padding-top:3px">If you do not have a will, go to<br><b>www.EasyWillPlan.org</b><br>In 20 minutes you can have a legal will for free.</div>
    <div class="abs" style="left:0;top:251px;width:205px;text-align:center;font-weight:700;font-size:7.4px;text-decoration:underline">CONTACT US</div>
    <p class="abs body-text" style="left:0;top:267px;width:205px;text-align:center">Have more question?<br>Please contact us at Meadowlark &amp; Allied Services</p>
    <svg class="abs" style="left:98px;top:286px" width="9" height="160" viewBox="0 0 9 160">
      <g fill="var(--green)"><circle cx="4.5" cy="4.5" r="4.5"/><circle cx="4.5" cy="33.5" r="4.5"/><circle cx="4.5" cy="56" r="4.5"/><circle cx="4.5" cy="79" r="4.5"/></g>
      <g fill="none" stroke="#fff" stroke-width=".8"><path d="M4.5 7 Q2.5 4.5 2.5 3.7 A2 2 0 0 1 6.5 3.7 Q6.5 4.5 4.5 7Z"/><path d="M3 31.5 Q3.5 35.5 6.5 36"/><rect x="2.5" y="54.5" width="4" height="3"/><circle cx="4.5" cy="79" r="2.3"/></g>
    </svg>
    <p class="abs body-text" style="left:0;top:297px;width:205px;text-align:center">1420 Prairie View Rd.<br>Suite 2, Fargo, ND&nbsp; 58102</p>
    <p class="abs body-text" style="left:0;top:326px;width:205px;text-align:center">701-555-0142 (ext. 100)</p>
    <p class="abs body-text" style="left:0;top:349px;width:205px;text-align:center">info@meadowlarkallied.org</p>
    <p class="abs body-text" style="left:0;top:372px;width:205px;text-align:center">www.meadowlarkallied.org</p>
    <div class="abs" style="left:0;top:400px;width:205px;text-align:center;font-weight:700;font-size:7.4px;color:var(--green);text-decoration:underline">Follow us:</div>
    <svg class="abs" style="left:73px;top:413px" width="60" height="12" viewBox="0 0 60 12">
      <path d="M11 6 H25 M35 6 H49" stroke="var(--green)" stroke-width=".8"/>
      <g fill="none" stroke="var(--green)" stroke-width="1.2"><circle cx="6" cy="6" r="5"/><circle cx="30" cy="6" r="5"/><circle cx="54" cy="6" r="5"/></g>
    </svg>
    <p class="abs" style="left:18px;top:440px;width:170px;text-align:center;font-size:3.4px;line-height:4.4px">This material has been prepared for informational purposes only and is not intended to provide tax, accounting, or legal advice. Meadowlark and Allied Services is not a professional fiduciary organization. Please consult with your tax advisor or financial professional before making a decision about Smart Giving.</p>
  </div>

  <!-- Front cover -->
  <div class="panel">
    <h1 class="abs" style="left:0;top:12px;width:205px;text-align:center;font-family:'Bebas Neue',sans-serif;font-weight:400;font-size:24px;line-height:24px;color:var(--green)">TRANSFORM YOUR GIVING</h1>
    <div class="abs" style="left:21px;top:38px;width:164px;height:14px;background:var(--purple);border-radius:7px;color:#fff;text-align:center;font-weight:700;font-size:10.4px;line-height:14px">BE STRATEGIC, BE SMART</div>
    <p class="abs" style="left:0;top:58px;width:205px;text-align:center;font-size:7.6px;line-height:10px">Discover the impact of Smart Giving with Meadowlark and Allied Services</p>
    <div class="photo" role="img" aria-label="Photo of a laughing older couple walking arm in arm through an autumn park" style="left:0;top:82px;width:205px;height:335px;background:linear-gradient(150deg,#6f7d4a 0%,#a9a06a 35%,#c98a5c 60%,#7b8fc6 80%,#8a6a48 100%)"></div>
    <svg class="abs" style="left:0;top:80px" width="205" height="45" viewBox="0 0 205 45">
      <path d="M0 0 H205 V3 Q130 45 20 12 L0 8Z" fill="#fff"/>
      <path d="M20 12 Q130 45 205 3 V12 Q130 52 20 12Z" fill="var(--green)"/>
    </svg>
    <g></g>
    <svg class="abs" style="left:0;top:100px" width="205" height="310" viewBox="0 0 205 310">
      <g fill="rgba(255,255,255,.35)" stroke="rgba(255,255,255,.8)" stroke-width=".6">
        <circle cx="39" cy="27" r="25"/><circle cx="164" cy="56" r="25"/><circle cx="39" cy="151" r="25"/><circle cx="164" cy="183" r="25"/><circle cx="39" cy="253" r="25"/>
      </g>
      <g font-family="Montserrat" font-weight="700" font-size="5.6" fill="var(--purple)" text-anchor="middle">
        <text x="39" y="43">Crypto</text><text x="164" y="72">DAF's</text><text x="39" y="168">Stocks &amp;</text><text x="39" y="174">Securities</text><text x="164" y="198">QCDs</text><text x="39" y="267">Charitable</text><text x="39" y="273">Annuity</text>
      </g>
      <g fill="var(--purple)"><rect x="31" y="140" width="3" height="8"/><rect x="36" y="136" width="3" height="12"/><rect x="41" y="138" width="3" height="10"/><rect x="46" y="133" width="3" height="15"/><rect x="156" y="170" width="16" height="14"/></g>
      <rect x="163" y="170" width="2" height="14" fill="#fff"/>
    </svg>
    <svg class="abs" style="left:0;top:383px" width="205" height="91" viewBox="0 0 205 91">
      <path d="M0 40 Q90 -20 205 30 V91 H0Z" fill="var(--purple)"/>
      <path d="M0 50 Q95 -5 205 40 V91 H0Z" fill="#fff"/>
    </svg>
    <div class="abs brand-name" style="left:0;top:434px;width:205px;font-size:14px;color:var(--purple)">Meadowlark &amp; Allied</div>
    <div class="abs" style="left:0;top:453px;width:205px;text-align:center;font-size:4.4px;font-weight:700;color:var(--purple);letter-spacing:.2px">MEADOWLARK AND ALLIED SERVICES, INC.</div>
  </div>
</section>

<!-- INSIDE -->
<section class="sheet sheet--inside">

  <!-- Stocks & DAF -->
  <div class="panel panel--purple">
    <p class="abs body-text" style="left:14px;top:16px;width:178px">We would like to introduce you to five Strategic and Smart ways to give that could potentially be more beneficial to you compared to traditional cash donations. We encourage you to keep this information as a guide for your future contributions.</p>
    <svg class="abs" style="left:14px;top:64px" width="36" height="31" viewBox="0 0 36 31" fill="var(--green)">
      <rect x="0" y="8" width="2.5" height="23"/><rect x="0" y="28.5" width="36" height="2.5"/>
      <rect x="6" y="18" width="4" height="9"/><rect x="13" y="13" width="4" height="14"/><rect x="20" y="16" width="4" height="11"/><rect x="27" y="10" width="4" height="17"/>
      <path d="M5 11 L12 5 L19 9 L30 1" fill="none" stroke="var(--green)" stroke-width="1.6"/>
    </svg>
    <div class="section-head" style="left:57px;top:60px;width:140px">Gifts of Stocks or Appreciated Assets Strategic &amp; Smart<em>Consider your long-term publicly traded stock as a way to give to your favorite charity.</em></div>
    <p class="abs body-text" style="left:14px;top:108px;width:180px">You can make a significantly bigger impact when you donate long-term appreciated securities, including stock, mutual funds, and bonds, directly to your favorite charity.</p>
    <div class="pill" style="left:14px;top:140px">HOW DOES IT WORK?</div>
    <p class="abs body-text" style="left:14px;top:167px;width:180px">When you donate stock to a charity, you will generally take a tax deduction for the full market value. Because you are donating stock, your contribution and tax deduction may be significantly higher than contributing the after-tax proceeds. The same benefits apply when you donate mutual funds or bonds.</p>
    <svg class="abs" style="left:15px;top:230px" width="36" height="36" viewBox="0 0 36 36" fill="none" stroke="var(--green)" stroke-width="1.2">
      <circle cx="13" cy="13" r="9"/><circle cx="13" cy="13" r="4"/><circle cx="24" cy="24" r="9"/><circle cx="24" cy="24" r="4"/>
    </svg>
    <div class="section-head" style="left:57px;top:232px;width:140px">Donor-Advised Fund (DAF) Strategic &amp; Smart<em>Consider a DAF – a simple, flexible, and tax-advantageous way to give to your favorite charities.</em></div>
    <p class="abs body-text" style="left:14px;top:279px;width:180px">A Donor-Advised Fund (DAF), is like a charitable investment account for the sole purpose of supporting your favorite charities.</p>
    <div class="pill" style="left:14px;top:309px">HOW DOES IT WORK?</div>
    <p class="abs body-text" style="left:14px;top:336px;width:180px">You establish a DAF and contribute cash, stocks, or non-publicly traded assets, cryptocurrency, and private company stock to be eligible for an immediate tax deduction. Those funds are contributed for tax-free growth. You can recommend grants be made from your DAF to any IRS qualified public charity.</p>
    <div class="photo" role="img" aria-label="Photo of a happy couple lying on the grass in a park" style="left:0;top:395px;width:205px;height:79px;background:linear-gradient(120deg,#7fae5a,#c9b68a 50%,#6f9a48)"></div>
    <svg class="abs" style="left:0;top:385px" width="205" height="89" viewBox="0 0 205 89">
      <path d="M0 0 H205 V89 Q120 25 0 20Z" fill="var(--purple-deep)"/>
      <path d="M0 12 Q120 14 205 89 L205 80 Q120 22 0 22Z" fill="var(--green)"/>
    </svg>
  </div>

  <!-- QCDs -->
  <div class="panel">
    <div class="photo" role="img" aria-label="Photo of an older couple on a sofa looking at a tablet together" style="left:0;top:0;width:205px;height:262px;background:linear-gradient(180deg,#e8e6e2 0%,#cfc3b8 40%,#b9a89a 65%,#ffffff 100%)"></div>
    <svg class="abs" style="left:14px;top:262px" width="30" height="38" viewBox="0 0 30 38" fill="var(--green)">
      <rect x="0" y="11" width="30" height="7"/><rect x="2" y="19" width="26" height="19"/>
      <rect x="13" y="11" width="4" height="27" fill="#fff"/>
      <path d="M15 11 Q5 -2 4 6 Q4 11 15 11 Q26 11 26 6 Q25 -2 15 11Z" fill="none" stroke="var(--green)" stroke-width="1.6"/>
    </svg>
    <div class="section-head" style="left:51px;top:262px;width:150px">Qualified Charitable Distributions (QCDs) Strategic &amp; Smart<em>Consider a QCD – when planning your IRA withdrawal strategy...and donate to your favorite charity.</em></div>
    <p class="abs body-text" style="left:13px;top:313px;width:182px">IRA owners at age 70 or over can transfer dollars from their IRA to charity tax-free each year. These transfers known as Qualified Charitable Distributions (QCDs) offer eligible older Americans a great way to easily give to charity.</p>
    <div class="pill" style="left:13px;top:360px">HOW DOES IT WORK?</div>
    <p class="abs body-text" style="left:13px;top:386px;width:182px">Are you 72 and required to take a minimum distribution (RMD) from your IRA but do not need the funds? Consider a Qualified Charitable Distribution. Normally, distributions from a traditional IRA are taxable when received. With a QCD, these distributions become tax-free when paid directly from the IRA to your favorite eligible charity. An IRA owner wishing to make a QCD should contact their IRA trustee, allowing time to complete the transaction before the end of the year to receive the tax benefit.</p>
  </div>

  <!-- Crypto & annuity -->
  <div class="panel panel--purple">
    <svg class="abs" style="left:16px;top:13px" width="32" height="28" viewBox="0 0 32 28" fill="none" stroke="var(--green)" stroke-width="1.2">
      <circle cx="8" cy="8" r="7"/><circle cx="24" cy="8" r="7"/><circle cx="16" cy="20" r="7"/>
      <text x="8" y="11" font-size="8" font-family="Montserrat" font-weight="700" text-anchor="middle" fill="var(--green)" stroke="none">B</text>
      <text x="24" y="11" font-size="8" font-family="Montserrat" font-weight="700" text-anchor="middle" fill="var(--green)" stroke="none">$</text>
    </svg>
    <div class="section-head" style="left:52px;top:13px;width:150px">Cryptocurrency Strategic &amp; Smart<em>Consider donating Bitcoin and other cryptocurrencies to your favorite charity.</em></div>
    <p class="abs body-text" style="left:15px;top:52px;width:180px">Bitcoin and other cryptocurrencies can be donated to charity just like other appreciated assets such as stocks and other business interests. Before you sell bitcoin and donate the after-tax proceeds, consider donating your bitcoin directly to a favorite charity.</p>
    <div class="pill" style="left:15px;top:98px">HOW DOES IT WORK?</div>
    <p class="abs body-text" style="left:15px;top:124px;width:180px">Many donors find it useful to open a Donor-Advised Fund (DAF). This strategy includes two significant benefits, both for you and your favorite charity.</p>
    <ul class="abs checklist body-text" style="left:15px;top:154px;width:180px">
      <li style="padding-left:13px;margin-bottom:7.5px">Your tax deduction will be equal to the fair market value of the donated bitcoin (as determined by a qualified appraisal).</li>
      <li style="padding-left:13px">Your cryptocurrency donation is tax-smart because it may eliminate capital gains taxes on the value /appreciation AND your favorite charity will receive 100% of the value of the contribution.</li>
    </ul>
    <p class="abs body-text" style="left:15px;top:224px;width:180px">Often charities are not able to accept direct donations of bitcoin/crypto so using a DAF is a great way to donate these assets.</p>
    <svg class="abs" style="left:15px;top:257px" width="32" height="32" viewBox="0 0 32 32" fill="var(--green)">
      <rect x="0" y="4" width="8" height="1.2"/><rect x="2" y="7" width="6" height="1.2"/>
      <ellipse cx="12" cy="28" rx="6" ry="2.5"/><ellipse cx="12" cy="24" rx="6" ry="2.5"/><ellipse cx="24" cy="28" rx="6" ry="2.5"/><ellipse cx="24" cy="24" rx="6" ry="2.5"/><ellipse cx="24" cy="20" rx="6" ry="2.5"/>
      <circle cx="23" cy="8" r="4"/>
    </svg>
    <div class="section-head" style="left:52px;top:260px;width:150px">Charitable Gift Annuity<br>Strategic &amp; Smart<em>Consider establishing a Charitable Gift Annuity</em></div>
    <p class="abs body-text" style="left:15px;top:302px;width:180px">You make a donation to a single charity. The gift is set aside in a reserve account and invested.</p>
    <div class="pill" style="left:15px;top:326px">HOW DOES IT WORK?</div>
    <p class="abs body-text" style="left:15px;top:351px;width:180px">A charitable gift annuity is a contract between a donor and a charity. As a donor, you make a sizable gift to charity using cash, securities, or possibly other assets. This money is then invested. In return, you become eligible to take a partial tax deduction for your donation, plus you receive a fixed stream of income from the charity for the rest of your life. At the end of your life (as well as your spouse's, if you're giving as a couple), the charity receives the remainder of the gift.</p>
    <svg class="abs" style="left:0;top:425px" width="205" height="49" viewBox="0 0 205 49">
      <path d="M0 49 Q80 5 205 8 V49Z" fill="#fff"/>
      <path d="M20 40 Q90 -2 205 0 V10 Q90 5 20 40Z" fill="var(--green)"/>
    </svg>
    <div class="abs" style="left:108px;top:454px;width:97px;height:13px;background:var(--purple);border-radius:6px 0 0 6px;color:#fff;font-size:6.4px;line-height:13px;text-align:center">www.meadowlarkallied.org</div>
  </div>
</section>

</body>
</html>
```